Year End Gift for Employees

Looking for assistance in creating an album cover. Here are some ideas that I have: Double Platinum, Lantern Crow Drifting, 2025 World Tour
QT/QR (name of the band) – on the front of the album cover
List of Songs - on the back of the album cover
Would like to have the ability to have team / individual pictures on the inside of the double platinum album cover
DON’T want anything gory or vulgar for the album cover
Also want rights to the image for the album cover to use for t-shirts
This is a Sales Team that work within Home Improvement Industries
Any additional images that you want to propose, I'm open too. Thanks and I'll await your response
Colleagues

```html
<!DOCTYPE html>
<html lang="en">
<head>
<meta charset="utf-8">
<title>QT/QR — 2025 World Tour Album Set</title>
<link rel="stylesheet" href="https://fonts.googleapis.com/css2?family=Oswald:wght@400;700&family=Mrs+Saint+Delafield&display=swap">
<style>
  :root {
    --backdrop: #8c8c8c;
    --steel-light: #dfe6ee;
    --steel-mid: #a9b6c4;
    --steel-dark: #7d8c9c;
    --mark-steel: #8896a6;
    --ink: #141414;
    --title-red: #d21f12;
    --shirt-black: #0b0b0b;
    --print-steel: #a3b0bf;
    --print-white: #ffffff;
  }
  * { box-sizing: border-box; margin: 0; padding: 0; }
  html, body { width: 1200px; height: 712px; overflow: hidden; }
  body { background: var(--backdrop); position: relative; font-family: "Oswald", sans-serif; }

  .steel {
    background:
      repeating-linear-gradient(0deg, rgba(255,255,255,.10) 0 1px, rgba(0,0,0,.05) 1px 2px, transparent 2px 3px),
      linear-gradient(135deg, var(--steel-dark) 0%, var(--steel-mid) 28%, var(--steel-light) 50%, var(--steel-mid) 72%, var(--steel-dark) 100%);
  }
  .cover { position: absolute; width: 302px; height: 302px; top: 37px; box-shadow: 2px 3px 6px rgba(0,0,0,.35); }
  .cover--front { left: 34px; }
  .cover--back { left: 369px; }
  svg { display: block; }

  .band-name { font-family: "Oswald", sans-serif; font-weight: 700; }
  .tour-script { font-family: "Mrs Saint Delafield", cursive; fill: var(--ink); }

  .tracklist {
    position: absolute; font-size: 13px; line-height: 19.3px; color: var(--ink);
    text-align: center; list-style: none; font-weight: 400; white-space: nowrap;
  }
  .tracklist--one { left: 20px; width: 126px; top: 80px; }
  .tracklist--two { left: 145px; width: 140px; top: 87px; }

  .disc { position: absolute; left: 189px; top: 373px; width: 300px; height: 300px; }

  .shirt-print { position: absolute; left: 740px; top: 150px; width: 420px; height: 440px; background: var(--shirt-black); }
</style>
</head>
<body>

<section class="cover cover--front steel" aria-label="Album front cover">
  <svg width="302" height="302" viewBox="0 0 302 302">
    <g class="band-name" font-size="130" fill="var(--mark-steel)">
      <text x="25" y="126" textLength="251" lengthAdjust="spacingAndGlyphs">QT/QR</text>
      <text x="25" y="277" textLength="251" lengthAdjust="spacingAndGlyphs">QT/QR</text>
    </g>
    <text class="tour-script" x="55" y="154" font-size="30" textLength="177" lengthAdjust="spacingAndGlyphs">2025 World Tour</text>
  </svg>
</section>

<section class="cover cover--back steel" aria-label="Album back cover">
  <svg width="302" height="70" viewBox="0 0 302 70" style="position:absolute;left:0;top:0">
    <text x="23" y="39" textLength="250" lengthAdjust="spacingAndGlyphs" font-family="Oswald, sans-serif" font-weight="700" font-size="35" fill="var(--title-red)">LANTERN CROW DRIFTING</text>
    <text class="tour-script" x="60" y="56" font-size="28" textLength="177" lengthAdjust="spacingAndGlyphs">2025 World Tour</text>
  </svg>
  <ol class="tracklist tracklist--one">
    <li>1. Song Name</li>
    <li>2. Another Song Name</li>
    <li>3. Song Name</li>
    <li>4. Even Longer Song Name</li>
    <li>5. Song Name</li>
    <li>6. Just a Song Name</li>
    <li>7. One More Song Name</li>
    <li>8. Song Name</li>
    <li>9. Song Name</li>
  </ol>
  <ol class="tracklist tracklist--two">
    <li>10. Song</li>
    <li>11. Maybe Song Name</li>
    <li>12. Pretty Song Name</li>
    <li>13. Another Name</li>
    <li>14. Song Name</li>
    <li>15. Yet another Song Name</li>
    <li>16. Song Name</li>
    <li>17. Last Name</li>
  </ol>
</section>

<section class="disc" aria-label="Disc label">
  <svg width="300" height="300" viewBox="0 0 300 300">
    <defs>
      <linearGradient id="disc-steel" x1="0" y1="0" x2="1" y2="1">
        <stop offset="0" stop-color="var(--steel-dark)"/>
        <stop offset=".3" stop-color="var(--steel-mid)"/>
        <stop offset=".5" stop-color="var(--steel-light)"/>
        <stop offset=".7" stop-color="var(--steel-mid)"/>
        <stop offset="1" stop-color="var(--steel-dark)"/>
      </linearGradient>
      <pattern id="brush" width="4" height="3" patternUnits="userSpaceOnUse">
        <rect width="4" height="1" fill="rgba(255,255,255,.12)"/>
      </pattern>
      <mask id="disc-hole">
        <rect width="300" height="300" fill="#000"/>
        <circle cx="150" cy="150" r="149" fill="#fff"/>
        <circle cx="150" cy="150" r="24" fill="#000"/>
      </mask>
    </defs>
    <g mask="url(#disc-hole)">
      <rect width="300" height="300" fill="url(#disc-steel)"/>
      <rect width="300" height="300" fill="url(#brush)"/>
      <g class="band-name" font-size="118" fill="var(--mark-steel)">
        <text x="41" y="128" textLength="214" lengthAdjust="spacingAndGlyphs">QT/QR</text>
        <text x="41" y="258" textLength="214" lengthAdjust="spacingAndGlyphs">QT/QR</text>
      </g>
      <text class="tour-script" x="234" y="144" font-size="26" text-anchor="middle">2025</text>
      <text class="tour-script" x="180" y="164" font-size="26" textLength="108" lengthAdjust="spacingAndGlyphs">World Tour</text>
    </g>
  </svg>
</section>

<section class="shirt-print" aria-label="T-shirt front print">
  <svg width="420" height="440" viewBox="0 0 420 440">
    <g class="band-name" font-size="84" fill="var(--print-steel)">
      <text x="123" y="175" textLength="172" lengthAdjust="spacingAndGlyphs">QT/QR</text>
      <text x="123" y="279" textLength="172" lengthAdjust="spacingAndGlyphs">QT/QR</text>
    </g>
    <text x="123" y="200" font-family="Mrs Saint Delafield, cursive" font-size="28" fill="var(--print-white)" textLength="175" lengthAdjust="spacingAndGlyphs">2025 World Tour</text>
  </svg>
</section>

</body>
</html>
```